Fire Risk Assessment App needs a sleek UI design

I need a sleek, modern but professional design for my 5 page Fire Risk Assessment App. Include gradient background, fire themed colours including reds, yellows, light orange and a touch of black. Design must ooze simplicity and professionalism. This is for the UK market. See attached images and word doc for more information.

Target Market(s)

General public and business owners

Industry/Entity Type

Technology / Fire Safety

Colors
00AB8E
00BBA5
67D7C9
C6EFE9
E9F9F6
59FF00
82FF00
B8FF75
E3FFCB
F4FFEA
FFC000
F8CF3A
FAE287
FDF2CF
FEFAEE
F0912C
F2A743
F7CA91
FBE8D2
FDF5EE
EE7325
F08F49
F5BC92
FAE3D3
FDF4ED
EB3D1F
EC4F4E
F09395
F8D3D4
FCEDEE

```html
<!DOCTYPE html>
<html lang="en">
<head>
<meta charset="utf-8">
<title>Fire Risk Assessment App – UI Screens</title>
<link href="https://fonts.googleapis.com/css2?family=Plus+Jakarta+Sans:wght@400;500;600;700&display=swap" rel="stylesheet">
<style>
:root{
  --navy:#1F2033;
  --navy-soft:#272940;
  --cream-top:#FEF8E4;
  --cream-bottom:#FBE6B2;
  --tabbar:#F8E4B0;
  --card:#FFFAEC;
  --ink:#1B1B1F;
  --muted:#5C564B;
  --orange:#F0912C;
  --orange-deep:#EE7325;
  --amber:#FFC000;
  --red:#EB3D1F;
  --red-soft:#EC4F4E;
  --green:#4FD600;
  --green-bright:#59FF00;
  --teal:#00BBA5;
  --teal-soft:#67D7C9;
  --white:#FFFFFF;
}
*{box-sizing:border-box;margin:0;padding:0}
html,body{width:1200px;height:1200px;overflow:hidden}
body{background:var(--navy);font-family:"Plus Jakarta Sans",sans-serif;color:var(--ink);position:relative}

.backdrop-word{position:absolute;left:68px;top:985px;font-size:150px;font-weight:500;letter-spacing:-4px;white-space:nowrap;color:var(--navy-soft);line-height:1}

.screen{position:absolute;width:231px;background:linear-gradient(180deg,var(--cream-top),var(--cream-bottom));overflow:hidden}
.screen-title{position:absolute;left:0;right:0;top:31px;text-align:center;font-size:15.5px;font-weight:500;line-height:19px}
.screen-sub{position:absolute;left:0;right:0;top:52px;text-align:center;font-size:8.5px;color:var(--muted)}

/* tab bar */
.tabbar{position:absolute;left:0;right:0;bottom:0;height:41px;background:var(--tabbar);display:flex;justify-content:space-around;align-items:center;padding:0 12px}
.tabbar .tab{width:20px;height:20px;display:flex;align-items:center;justify-content:center;position:relative;color:#2A2A2E}
.tabbar .tab.is-active{color:var(--orange-deep)}
.tabbar .tab.is-active::before{content:"";position:absolute;top:-12px;left:-3px;width:26px;height:2px;border-radius:2px;background:var(--orange-deep)}
.tabbar svg{width:15px;height:15px}

/* shared round badge inside pill buttons */
.btn-icon{flex:none;width:23px;height:23px;border-radius:50%;margin-left:3px;display:flex;align-items:center;justify-content:center;background:#F5962E;color:var(--white)}
.btn-icon svg{width:10px;height:10px}
.btn-label{flex:1;text-align:center;padding-right:26px}

/* welcome */
.hero-title{position:absolute;left:0;right:0;top:33px;text-align:center;font-size:15px;line-height:18px;font-weight:500}
.hero-title em{font-style:normal;color:var(--red);font-weight:700}
.hero-visual{position:absolute;left:54px;top:101px;width:126px;height:224px;border-radius:9px;background:linear-gradient(165deg,#F58A25,#F5A628 70%,#FBC94A)}
.hero-note{position:absolute;left:0;right:0;top:339px;text-align:center;font-size:8.3px;color:var(--muted)}
.pill{position:absolute;left:41px;width:150px;height:29px;border-radius:15px;display:flex;align-items:center;font-size:8.8px;font-weight:500}
.pill .btn-icon{background:var(--orange)}
.pill .btn-icon svg{width:11px;height:11px}
.pill-create{top:361px;background:linear-gradient(90deg,var(--red),#F07A2A);color:var(--white);box-shadow:0 4px 10px rgba(235,61,31,.3)}
.pill-create .btn-icon{background:#F5962E}
.pill-login{top:428px;border:1px solid var(--red);color:var(--ink)}
.hero-tagline{position:absolute;left:0;right:0;top:405px;text-align:center;font-size:8.5px;color:var(--muted)}
.hero-tagline em{font-style:normal;color:var(--red)}
.hero-credit{position:absolute;left:0;right:0;top:471px;text-align:center;font-size:7.8px;color:#8A8170}

/* dashboard */
.start-ring{position:absolute;left:45px;top:73px;width:142px;height:142px;border-radius:50%;border:13px solid rgba(244,214,150,.35)}
.start-button{position:absolute;left:77px;top:105px;width:78px;height:78px;border-radius:50%;background:radial-gradient(circle at 50% 40%,#FFB41C,#F58420 65%,#EE6A1E);box-shadow:0 7px 16px rgba(238,115,37,.45);display:flex;align-items:center;justify-content:center}
.start-button svg{width:16px;height:16px}
.status-tabs{position:absolute;left:0;right:0;top:212px;font-size:9px;color:var(--muted)}
.status-tabs span{position:absolute;transform:translateX(-50%);white-space:nowrap}
.status-tabs .is-active{color:var(--red);font-weight:500}
.section-label{position:absolute;left:10px;font-size:8.8px;color:var(--red);font-weight:500}
.list-card{position:absolute;left:10px;width:211px;border-radius:8px;background:var(--card);padding:0 10px;display:flex;flex-direction:column;justify-content:center;box-shadow:0 2px 6px rgba(210,160,70,.12)}
.list-card h3{font-size:8.8px;font-weight:600;line-height:12px}
.list-card p{font-size:8.3px;color:var(--muted);line-height:12px;margin-top:2px}
.list-card .status{position:absolute;right:10px;top:50%;transform:translateY(-50%)}

/* purchase */
.plans{position:absolute;left:10px;width:212px;border-radius:12px;background:linear-gradient(200deg,var(--red) 0%,#F07526 35%,#F5982C 100%);padding:14px 11px 0}
.plans h2{text-align:center;color:var(--white);font-size:9.8px;font-weight:500;line-height:12px;margin-bottom:9px}
.plan{position:relative;height:62px;border-radius:7px;background:rgba(255,255,255,.17);margin-bottom:6px;color:var(--white);text-align:center;display:flex;flex-direction:column;justify-content:center}
.plan::before{content:"";position:absolute;left:8px;top:8px;width:14px;height:14px;border-radius:50%;border:1px solid rgba(255,255,255,.85)}
.plan-name{font-size:8.6px;font-weight:500}
.plan-count{font-size:6px;opacity:.85;margin-top:2px}
.plan-price{font-size:8.5px;font-weight:700;margin-top:3px}
.plan-price s{font-weight:400;font-size:7px;opacity:.6;margin-left:3px}
.plans-stacked .plan-price s{display:block;margin:3px 0 0}
.checkout{position:relative;height:29px;border-radius:15px;background:linear-gradient(90deg,#E8411F,#F07A2A);display:flex;align-items:center;color:var(--white);font-size:8.8px;box-shadow:0 4px 10px rgba(150,40,10,.25);margin:10px 0 14px}

/* question */
.section-head{position:absolute;left:10px;top:34px;width:211px;height:101px;border-radius:10px;background:linear-gradient(200deg,var(--red),#F07526 45%,#F6A02C);color:var(--white);padding:11px 16px}
.section-head .meta{font-size:8.5px;line-height:12.5px}
.section-head hr{border:0;border-top:1px solid rgba(255,255,255,.35);margin:7px 0 9px}
.section-head .clause-title{font-size:7.8px;font-weight:700;color:#FFE9A0}
.section-head .clause-ref{font-size:7.8px;opacity:.9;margin-top:2px}
.section-head .badge{position:absolute;right:10px}
.question-card{position:absolute;left:10px;top:162px;width:211px;height:281px;border-radius:10px;background:rgba(255,250,236,.85);padding:0 16px}
.bolt{position:absolute;left:97px;top:142px;width:38px;height:38px;border-radius:50%;background:radial-gradient(circle at 50% 40%,#FFB41C,#F07A20);box-shadow:0 4px 10px rgba(238,115,37,.4);display:flex;align-items:center;justify-content:center;z-index:2}
.bolt svg{width:14px;height:14px}
.q-num{position:absolute;left:16px;top:25px;font-size:7.5px;color:var(--muted)}
.q-text{position:absolute;left:16px;right:14px;top:38px;font-size:9.6px;font-weight:500;line-height:12px}
.answers{position:absolute;left:16px;top:70px;display:flex;gap:6px}
.answer{width:31px;height:31px;border-radius:5px;background:var(--white);display:flex;align-items:center;justify-content:center}
.answer.is-selected{border:1px solid var(--orange-deep)}
.answer svg{width:13px;height:13px}
.note-field{position:absolute;left:16px;top:112px;width:179px;height:20px;border-radius:4px;background:var(--white);font-size:7.6px;color:var(--muted);display:flex;align-items:center;justify-content:center}
.evidence-photo{position:absolute;left:16px;top:144px;width:179px;height:82px;border-radius:5px;background:linear-gradient(135deg,#D9D9DC,#8E8E93)}
.q-actions{position:absolute;left:16px;top:238px;display:flex;gap:9px}
.q-btn{width:85px;height:28px;border-radius:14px;display:flex;align-items:center;font-size:8.3px}
.q-btn .ico{flex:none;width:22px;height:22px;border-radius:50%;display:flex;align-items:center;justify-content:center;margin:0 3px}
.q-btn .ico svg{width:10px;height:10px}
.q-save{border:1px solid var(--orange-deep);background:rgba(255,255,255,.5)}
.q-save .ico{background:var(--orange)}
.q-save .q-label{margin-left:3px}
.q-next{background:linear-gradient(90deg,var(--teal-soft),#5CE46E);justify-content:space-between;padding-left:25px}
.q-next .ico{background:rgba(255,255,255,.35)}

/* support */
.message-box{position:absolute;left:11px;top:76px;width:210px;height:126px;border-radius:9px;border:1px solid #F4DDA8;background:rgba(255,251,238,.7);padding:13px 14px;font-size:7.8px;color:var(--muted)}
.message-box .mic{position:absolute;right:8px;bottom:10px;width:24px;height:24px;border-radius:50%;background:radial-gradient(circle at 50% 40%,#FFB41C,#F07A20);display:flex;align-items:center;justify-content:center}
.message-box .mic svg{width:10px;height:10px}
.send{position:absolute;left:11px;top:210px;width:210px;height:29px;border-radius:15px;background:linear-gradient(90deg,var(--red),#F08A2C);display:flex;align-items:center;color:var(--white);font-size:8.8px}
.flame-art{position:absolute;left:0;right:0;top:300px;height:160px;background:radial-gradient(ellipse at 50% 90%,rgba(247,170,90,.35),rgba(250,220,150,0) 70%)}
</style>
</head>
<body>

<div class="backdrop-word" aria-hidden="true">Fire Risk Assessment</div>

<!-- Welcome -->
<section class="screen" style="left:99px;top:65px;height:501px">
  <h1 class="hero-title">The Most <em>User Friendly</em><br>Fire Risk Assessment App<br>Available</h1>
  <div class="hero-visual" role="img" aria-label="Stacked assessment cards showing a fire hazard question in progress"></div>
  <p class="hero-note">Quick tap response and voice activated typing</p>
  <div class="pill pill-create">
    <span class="btn-icon"><svg viewBox="0 0 12 12" fill="currentColor"><circle cx="5" cy="3.5" r="2.3"/><path d="M1 11c0-2.4 1.8-4 4-4s4 1.6 4 4z"/><path d="M9.5 3v3M8 4.5h3" stroke="currentColor" stroke-width="1.1"/></svg></span>
    <span class="btn-label">Create a Free Account</span>
  </div>
  <p class="hero-tagline">Any <em>responsible person</em> can do it.</p>
  <div class="pill pill-login">
    <span class="btn-icon"><svg viewBox="0 0 12 12" fill="currentColor"><circle cx="5" cy="3.5" r="2.3"/><path d="M1 11c0-2.4 1.8-4 4-4s4 1.6 4 4z"/></svg></span>
    <span class="btn-label">Customer Login</span>
  </div>
  <p class="hero-credit">Created and endorsed by Northvale Firefighters</p>
</section>

<!-- Dashboard: completed -->
<section class="screen" style="left:355px;top:65px;height:512px">
  <h2 class="screen-title">Dashboard</h2>
  <p class="screen-sub">Start Fire Assessment</p>
  <div class="start-ring"></div>
  <div class="start-button"><svg viewBox="0 0 16 16"><path d="M8 2v12M2 8h12" stroke="#fff" stroke-width="2.6" stroke-linecap="round"/></svg></div>
  <div class="status-tabs"><span class="is-active" style="left:83px">Completed</span><span style="left:150px">In Progress</span></div>
  <article class="list-card" style="top:233px;height:41px"><h3>Ned’s Barbershop</h3><p>Lorem Ipsum is simply dummy text</p>
    <svg class="status" width="13" height="13" viewBox="0 0 14 14"><circle cx="7" cy="7" r="7" fill="var(--green)"/><path d="M4 7.2l2 2 4-4" stroke="#fff" stroke-width="1.5" fill="none"/></svg></article>
  <article class="list-card" style="top:283px;height:41px"><h3>Ned’s Barbershop</h3><p>Lorem Ipsum is simply dummy text</p>
    <svg class="status" width="13" height="13" viewBox="0 0 14 14"><circle cx="7" cy="7" r="7" fill="var(--green)"/><path d="M4 7.2l2 2 4-4" stroke="#fff" stroke-width="1.5" fill="none"/></svg></article>
  <p class="section-label" style="top:339px">Purchases</p>
  <article class="list-card" style="top:365px;height:42px"><h3>Residential Fire Risk Assessment</h3><p>Lorem Ipsum is sim ply dummy text</p></article>
  <article class="list-card" style="top:415px;height:41px"><h3>Commercial Fire Risk Assessment</h3><p>Lorem Ipsum is sim ply dummy text</p></article>
  <nav class="tabbar">
    <span class="tab is-active"><svg viewBox="0 0 16 16" fill="none" stroke="currentColor" stroke-width="2"><path d="M3 13a6 6 0 1 1 10 0"/><path d="M8 9l2.5-3"/></svg></span>
    <span class="tab"><svg viewBox="0 0 16 16" fill="currentColor"><rect x="1" y="3" width="14" height="10" rx="2"/><rect x="1" y="6" width="14" height="1.6" fill="var(--tabbar)"/></svg></span>
    <span class="tab"><svg viewBox="0 0 16 16" fill="currentColor"><path d="M3 2h10a2 2 0 0 1 2 2v6a2 2 0 0 1-2 2H8l-3 3v-3H3a2 2 0 0 1-2-2V4a2 2 0 0 1 2-2z"/><rect x="5" y="6.3" width="6" height="1.4" fill="var(--tabbar)"/></svg></span>
    <span class="tab"><svg viewBox="0 0 16 16" fill="currentColor"><circle cx="6" cy="4.5" r="3"/><path d="M1 15c0-3.2 2.2-5.5 5-5.5s5 2.3 5 5.5z"/><path d="M11 12h4m-1.5-1.5L15 12l-1.5 1.5" stroke="currentColor" stroke-width="1.2" fill="none"/></svg></span>
  </nav>
</section>

<!-- Dashboard: in progress -->
<section class="screen" style="left:612px;top:65px;height:512px">
  <h2 class="screen-title">Dashboard</h2>
  <p class="screen-sub">Start Fire Assessment</p>
  <div class="start-ring"></div>
  <div class="start-button"><svg viewBox="0 0 16 16"><path d="M8 2v12M2 8h12" stroke="#fff" stroke-width="2.6" stroke-linecap="round"/></svg></div>
  <div class="status-tabs"><span style="left:81px">Completed</span><span class="is-active" style="left:149px">In Progress</span></div>
  <article class="list-card" style="top:234px;height:43px"><h3>Elm Road School</h3><p>Lorem Ipsum is simply dummy text</p>
    <svg class="status" width="24" height="24" viewBox="0 0 24 24"><circle cx="12" cy="12" r="11" fill="#fff"/><path d="M12 1a11 11 0 0 1 10.5 7.6" stroke="var(--green-bright)" stroke-width="2" fill="none"/><text x="12" y="14.5" text-anchor="middle" font-size="6.5" font-family="Plus Jakarta Sans, sans-serif">30%</text></svg></article>
  <article class="list-card" style="top:286px;height:43px"><h3>Willow Court Nursing Home</h3><p>Lorem Ipsum is simply dummy text</p>
    <svg class="status" width="24" height="24" viewBox="0 0 24 24"><circle cx="12" cy="12" r="11" fill="#fff"/><path d="M12 1a11 11 0 0 1 6.5 19.9" stroke="var(--green-bright)" stroke-width="2" fill="none"/><text x="12" y="14.5" text-anchor="middle" font-size="6.5" font-family="Plus Jakarta Sans, sans-serif">40%</text></svg></article>
  <p class="section-label" style="top:345px">Purchases</p>
  <article class="list-card" style="top:371px;height:41px"><h3>Residential Fire Risk Assessment</h3><p>Lorem Ipsum is sim ply dummy text</p></article>
  <article class="list-card" style="top:420px;height:42px"><h3>Commercial Fire Risk Assessment</h3><p>Lorem Ipsum is sim ply dummy text</p></article>
  <nav class="tabbar">
    <span class="tab is-active"><svg viewBox="0 0 16 16" fill="none" stroke="currentColor" stroke-width="2"><path d="M3 13a6 6 0 1 1 10 0"/><path d="M8 9l2.5-3"/></svg></span>
    <span class="tab"><svg viewBox="0 0 16 16" fill="currentColor"><rect x="1" y="3" width="14" height="10" rx="2"/><rect x="1" y="6" width="14" height="1.6" fill="var(--tabbar)"/></svg></span>
    <span class="tab"><svg viewBox="0 0 16 16" fill="currentColor"><path d="M3 2h10a2 2 0 0 1 2 2v6a2 2 0 0 1-2 2H8l-3 3v-3H3a2 2 0 0 1-2-2V4a2 2 0 0 1 2-2z"/><rect x="5" y="6.3" width="6" height="1.4" fill="var(--tabbar)"/></svg></span>
    <span class="tab"><svg viewBox="0 0 16 16" fill="currentColor"><circle cx="6" cy="4.5" r="3"/><path d="M1 15c0-3.2 2.2-5.5 5-5.5s5 2.3 5 5.5z"/><path d="M11 12h4m-1.5-1.5L15 12l-1.5 1.5" stroke="currentColor" stroke-width="1.2" fill="none"/></svg></span>
  </nav>
</section>

<!-- Purchase: inline prices -->
<section class="screen" style="left:868px;top:65px;height:501px">
  <h2 class="screen-title">Purchase</h2>
  <p class="screen-sub">Lorem Ipsum is simply dummy text</p>
  <div class="plans" style="top:77px">
    <h2>FIRE RISK ASSESSMENT<br>PAYMENT OPTIONS</h2>
    <div class="plan"><span class="plan-name">BRONZE</span><span class="plan-count">1 Fire Risk Assessment</span><span class="plan-price">£19.99</span></div>
    <div class="plan"><span class="plan-name">SILVER</span><span class="plan-count">3 Fire Risk Assessment</span><span class="plan-price">£54.99<s>£59.97</s></span></div>
    <div class="plan"><span class="plan-name">GOLD</span><span class="plan-count">5 Fire Risk Assessment</span><span class="plan-price">£89.99<s>£99.95</s></span></div>
    <div class="plan"><span class="plan-name">PLATINUM</span><span class="plan-count">10 Fire Risk Assessment</span><span class="plan-price">£174.99<s>£199.90</s></span></div>
    <div class="checkout"><span class="btn-icon"><svg viewBox="0 0 10 10" fill="#fff"><rect x="1" y="3" width="8" height="6" rx="1"/><path d="M3.5 3V2a1.5 1.5 0 0 1 3 0v1" stroke="#fff" fill="none"/></svg></span><span class="btn-label">Checkout</span></div>
  </div>
  <nav class="tabbar">
    <span class="tab"><svg viewBox="0 0 16 16" fill="none" stroke="currentColor" stroke-width="2"><path d="M3 13a6 6 0 1 1 10 0"/><path d="M8 9l2.5-3"/></svg></span>
    <span class="tab is-active"><svg viewBox="0 0 16 16" fill="currentColor"><rect x="1" y="3" width="14" height="10" rx="2"/><rect x="1" y="6" width="14" height="1.6" fill="var(--tabbar)"/></svg></span>
    <span class="tab"><svg viewBox="0 0 16 16" fill="currentColor"><path d="M3 2h10a2 2 0 0 1 2 2v6a2 2 0 0 1-2 2H8l-3 3v-3H3a2 2 0 0 1-2-2V4a2 2 0 0 1 2-2z"/><rect x="5" y="6.3" width="6" height="1.4" fill="var(--tabbar)"/></svg></span>
    <span class="tab"><svg viewBox="0 0 16 16" fill="currentColor"><circle cx="6" cy="4.5" r="3"/><path d="M1 15c0-3.2 2.2-5.5 5-5.5s5 2.3 5 5.5z"/><path d="M11 12h4m-1.5-1.5L15 12l-1.5 1.5" stroke="currentColor" stroke-width="1.2" fill="none"/></svg></span>
  </nav>
</section>

<!-- Purchase: stacked prices -->
<section class="screen" style="left:227px;top:616px;height:499px">
  <h2 class="screen-title">Purchase</h2>
  <p class="screen-sub">Lorem Ipsum is simply dummy text</p>
  <div class="plans plans-stacked" style="top:76px">
    <h2>FIRE RISK ASSESSMENT<br>PAYMENT OPTIONS</h2>
    <div class="plan"><span class="plan-name">BRONZE</span><span class="plan-count">1 Fire Risk Assessment</span><span class="plan-price">£19.99</span></div>
    <div class="plan"><span class="plan-name">SILVER</span><span class="plan-count">3 Fire Risk Assessment</span><span class="plan-price">£54.99<s>£59.97</s></span></div>
    <div class="plan"><span class="plan-name">GOLD</span><span class="plan-count">5 Fire Risk Assessment</span><span class="plan-price">£89.99<s>£99.95</s></span></div>
    <div class="plan"><span class="plan-name">PLATINUM</span><span class="plan-count">10 Fire Risk Assessment</span><span class="plan-price">£174.99<s>£199.90</s></span></div>
    <div class="checkout"><span class="btn-icon"><svg viewBox="0 0 10 10" fill="#fff"><rect x="1" y="3" width="8" height="6" rx="1"/><path d="M3.5 3V2a1.5 1.5 0 0 1 3 0v1" stroke="#fff" fill="none"/></svg></span><span class="btn-label">Checkout</span></div>
  </div>
  <nav class="tabbar">
    <span class="tab"><svg viewBox="0 0 16 16" fill="none" stroke="currentColor" stroke-width="2"><path d="M3 13a6 6 0 1 1 10 0"/><path d="M8 9l2.5-3"/></svg></span>
    <span class="tab is-active"><svg viewBox="0 0 16 16" fill="currentColor"><rect x="1" y="3" width="14" height="10" rx="2"/><rect x="1" y="6" width="14" height="1.6" fill="var(--tabbar)"/></svg></span>
    <span class="tab"><svg viewBox="0 0 16 16" fill="currentColor"><path d="M3 2h10a2 2 0 0 1 2 2v6a2 2 0 0 1-2 2H8l-3 3v-3H3a2 2 0 0 1-2-2V4a2 2 0 0 1 2-2z"/><rect x="5" y="6.3" width="6" height="1.4" fill="var(--tabbar)"/></svg></span>
    <span class="tab"><svg viewBox="0 0 16 16" fill="currentColor"><circle cx="6" cy="4.5" r="3"/><path d="M1 15c0-3.2 2.2-5.5 5-5.5s5 2.3 5 5.5z"/><path d="M11 12h4m-1.5-1.5L15 12l-1.5 1.5" stroke="currentColor" stroke-width="1.2" fill="none"/></svg></span>
  </nav>
</section>

<!-- Assessment question -->
<section class="screen" style="left:483px;top:616px;height:499px">
  <header class="section-head">
    <p class="meta">Fire Risk Assessment<br>Fire Hazards<br>Section: 7.00/30.00</p>
    <svg class="badge" style="top:12px" width="26" height="26" viewBox="0 0 26 26"><circle cx="13" cy="13" r="12" fill="#fff"/><path d="M13 1a12 12 0 0 1 11.4 8.3" stroke="var(--green-bright)" stroke-width="2.2" fill="none"/><text x="13" y="15.5" text-anchor="middle" font-size="7" fill="#1B1B1F" font-family="Plus Jakarta Sans, sans-serif">30%</text></svg>
    <hr>
    <p class="clause-title">ELECTRONIC SOURCES OF IGNITION</p>
    <p class="clause-ref">(Clause 13 &amp; Annex B)</p>
    <svg class="badge" style="top:63px" width="25" height="25" viewBox="0 0 25 25"><circle cx="12.5" cy="12.5" r="11" fill="#fff" stroke="var(--green-bright)" stroke-width="2"/><rect x="8" y="8.5" width="9" height="8" rx="1.5" fill="none" stroke="#bbb"/><circle cx="11" cy="11.5" r="1" fill="#bbb"/></svg>
  </header>
  <div class="bolt"><svg viewBox="0 0 14 14"><path d="M8 1L3 8h4l-1 5 5-7H7z" fill="#2A1A10"/></svg></div>
  <div class="question-card">
    <p class="q-num">Q: 7.01</p>
    <p class="q-text">Are resonable measure taken to prevent fire of electrical origin?</p>
    <div class="answers">
      <span class="answer"><svg viewBox="0 0 14 14"><circle cx="7" cy="7" r="6.5" fill="var(--teal)"/><path d="M4 7.2l2 2 4-4" stroke="#fff" stroke-width="1.4" fill="none"/></svg></span>
      <span class="answer"><svg viewBox="0 0 14 14"><circle cx="7" cy="7" r="6.5" fill="var(--red)"/><path d="M4.8 4.8l4.4 4.4M9.2 4.8l-4.4 4.4" stroke="#fff" stroke-width="1.4"/></svg></span>
      <span class="answer is-selected"><svg viewBox="0 0 14 14"><circle cx="7" cy="7" r="6.5" fill="var(--orange)"/><path d="M4.3 7h5.4" stroke="#fff" stroke-width="1.4"/></svg></span>
      <span class="answer"><svg viewBox="0 0 14 14"><path d="M1.5 4.5h3l1-1.5h3l1 1.5h3v7.5h-11z" fill="var(--amber)"/><circle cx="7" cy="8" r="2" fill="#fff"/></svg></span>
      <span class="answer"><svg viewBox="0 0 14 14" fill="none" stroke="var(--orange-deep)" stroke-width="1.3"><rect x="5" y="1.5" width="4" height="7" rx="2" fill="var(--orange-deep)"/><path d="M3 6.5a4 4 0 0 0 8 0M7 10.5V13M5 13h4"/></svg></span>
    </div>
    <div class="note-field">No, electric sockets are overloaded</div>
    <div class="evidence-photo" role="img" aria-label="Photo evidence of a burning electrical cabinet"></div>
    <div class="q-actions">
      <span class="q-btn q-save"><span class="ico"><svg viewBox="0 0 10 10" fill="none" stroke="#fff" stroke-width="1.3"><path d="M3 2L1 4l2 2"/><path d="M1 4h5a3 3 0 0 1 0 6H4"/></svg></span><span class="q-label">Save &amp; Exit</span></span>
      <span class="q-btn q-next"><span class="q-label">Next</span><span class="ico"><svg viewBox="0 0 10 10" fill="none" stroke="#1B1B1F" stroke-width="1.2"><path d="M1 5h8M6 2l3 3-3 3"/></svg></span></span>
    </div>
  </div>
  <nav class="tabbar">
    <span class="tab"><svg viewBox="0 0 16 16" fill="none" stroke="currentColor" stroke-width="2"><path d="M3 13a6 6 0 1 1 10 0"/><path d="M8 9l2.5-3"/></svg></span>
    <span class="tab"><svg viewBox="0 0 16 16" fill="currentColor"><rect x="1" y="3" width="14" height="10" rx="2"/><rect x="1" y="6" width="14" height="1.6" fill="var(--tabbar)"/></svg></span>
    <span class="tab"><svg viewBox="0 0 16 16" fill="currentColor"><path d="M3 2h10a2 2 0 0 1 2 2v6a2 2 0 0 1-2 2H8l-3 3v-3H3a2 2 0 0 1-2-2V4a2 2 0 0 1 2-2z"/><rect x="5" y="6.3" width="6" height="1.4" fill="var(--tabbar)"/></svg></span>
    <span class="tab"><svg viewBox="0 0 16 16" fill="currentColor"><circle cx="6" cy="4.5" r="3"/><path d="M1 15c0-3.2 2.2-5.5 5-5.5s5 2.3 5 5.5z"/><path d="M11 12h4m-1.5-1.5L15 12l-1.5 1.5" stroke="currentColor" stroke-width="1.2" fill="none"/></svg></span>
  </nav>
</section>

<!-- Technical support -->
<section class="screen" style="left:738px;top:616px;height:499px">
  <h2 class="screen-title">Technical Support</h2>
  <p class="screen-sub">Type/Record Your Response Here</p>
  <div class="message-box">Write your message here...
    <span class="mic"><svg viewBox="0 0 10 10" fill="none" stroke="#fff" stroke-width="1"><rect x="3.5" y="0.8" width="3" height="5" rx="1.5" fill="#fff"/><path d="M2 4.5a3 3 0 0 0 6 0M5 7.5V9.3"/></svg></span>
  </div>
  <div class="send"><span class="btn-icon"><svg viewBox="0 0 10 10" fill="#fff"><path d="M9.5 0.5L0.5 4.5l3.5 1.2L5.3 9.5z"/></svg></span><span class="btn-label">Send</span></div>
  <div class="flame-art" role="img" aria-label="Soft flame illustration"></div>
  <nav class="tabbar">
    <span class="tab"><svg viewBox="0 0 16 16" fill="none" stroke="currentColor" stroke-width="2"><path d="M3 13a6 6 0 1 1 10 0"/><path d="M8 9l2.5-3"/></svg></span>
    <span class="tab"><svg viewBox="0 0 16 16" fill="currentColor"><rect x="1" y="3" width="14" height="10" rx="2"/><rect x="1" y="6" width="14" height="1.6" fill="var(--tabbar)"/></svg></span>
    <span class="tab is-active"><svg viewBox="0 0 16 16" fill="currentColor"><path d="M3 2h10a2 2 0 0 1 2 2v6a2 2 0 0 1-2 2H8l-3 3v-3H3a2 2 0 0 1-2-2V4a2 2 0 0 1 2-2z"/><rect x="5" y="6.3" width="6" height="1.4" fill="var(--tabbar)"/></svg></span>
    <span class="tab"><svg viewBox="0 0 16 16" fill="currentColor"><circle cx="6" cy="4.5" r="3"/><path d="M1 15c0-3.2 2.2-5.5 5-5.5s5 2.3 5 5.5z"/><path d="M11 12h4m-1.5-1.5L15 12l-1.5 1.5" stroke="currentColor" stroke-width="1.2" fill="none"/></svg></span>
  </nav>
</section>

</body>
</html>
```